Money Mindset Podcast needs fun, creative cover art

Launching a new podcast called 'Turning Your Thoughts Toward Savings' - aimed at an audience 30-50 who are interested in the practicalities of managing their money but also the more mental and emotional aspects.
Looking for something not too serious, warm and friendly.

Must be easy to read on phone screens
3000 x 3000 in size
Avoid currency symbols $, £ etc, as may have an international audience

Target Market(s)

Podcast listeners age 30-50 starting in the UK but then worldwide. Probably 60:40 female bias

Industry/Entity Type

Life Coaching

Font styles to use
Serif
Sans Serif

Colors
cadf82
fee18a
acd037
85cae6
eea4c8
f59195
85acd3

Requirements
Must have
• Simple, clear design. Easy to read on variety of devices. 3000 x 3000
Appeal to those with a spiritual or emotional interests
Nice to have
• Stand out among other money related podcasts
Maybe play around with clouds, lightbulbs and clearing skies
Should not have
• Currency symbols such as $ or £
Be too corporate or bank like
Stock images

```html
<!DOCTYPE html>
<html lang="en">
<head>
<meta charset="utf-8">
<title>Turning Your Thoughts Toward Savings — Podcast Cover</title>
<link rel="stylesheet" href="https://fonts.googleapis.com/css2?family=Bebas+Neue&display=swap">
<style>
  :root {
    --ring-1: #9c2630;
    --ring-2: #b9313c;
    --ring-3: #d3434e;
    --ring-4: #e65a63;
    --ring-5: #f17078;
    --ring-6: #f78a90;
    --board-light: #5fb4f5;
    --board-main: #3c9cec;
    --board-deep: #2a7fd0;
    --type: #ffffff;
    --type-shadow: rgba(16, 40, 80, 0.45);
  }
  * { margin: 0; padding: 0; box-sizing: border-box; }
  html, body { width: 1200px; height: 1200px; overflow: hidden; }
  body { background: var(--ring-6); }

  .cover {
    position: relative;
    width: 1200px;
    height: 1200px;
    overflow: hidden;
    background: radial-gradient(circle at 0 0,
      var(--ring-1) 0 480px,
      var(--ring-2) 480px 760px,
      var(--ring-3) 760px 1020px,
      var(--ring-4) 1020px 1280px,
      var(--ring-5) 1280px 1520px,
      var(--ring-6) 1520px);
  }

  .sign-art {
    position: absolute;
    left: 105px;
    top: 384px;
    width: 980px;
    height: 680px;
    border-radius: 36px;
    background: linear-gradient(115deg, var(--board-light) 0%, var(--board-main) 45%, var(--board-deep) 100%);
  }

  .sign-title {
    position: absolute;
    left: 105px;
    top: 384px;
    width: 980px;
    height: 680px;
    display: flex;
    flex-direction: column;
    align-items: center;
    justify-content: center;
    font-family: "Bebas Neue", "Oswald", sans-serif;
    font-weight: 400;
    font-size: 150px;
    line-height: 0.98;
    text-align: center;
    color: var(--type);
    letter-spacing: 1px;
    text-shadow: 5px 6px 0 var(--type-shadow);
    white-space: nowrap;
  }
  .sign-title span { display: block; }
</style>
</head>
<body>
  <main class="cover">
    <div class="sign-art" role="img" aria-label="Illustration of a blue sign hanging from a pin on a string"></div>
    <h1 class="sign-title">
      <span>Turning Your</span>
      <span>Thoughts Toward</span>
      <span>Savings</span>
    </h1>
  </main>
</body>
</html>
```